Pellmora Business Cards

Create new business cards with the details below.

Stuart Kovan
Director

MB: +61 427 315 964
PH: 1300 647 519
Email: stuart.kovan@pellmora.com.au
Address: 27D Halden Parade, Brookvale VIC 3174 Australia
Website: www.pellmora.com.au

Target Market(s)

Other business

Industry/Entity Type

Business

Requirements
Must have
• must be clean looking

```html
<!DOCTYPE html>
<html lang="en">
<head>
<meta charset="utf-8">
<title>Pellmora Business Cards</title>
<link rel="stylesheet" href="https://fonts.googleapis.com/css2?family=Jost:ital,wght@0,300;0,400;0,600;0,700;1,400;1,600&display=swap">
<style>
  :root {
    --bg: #a7a7a7;
    --card: #ffffff;
    --lime: #a6c93a;
    --charcoal: #2e2e2e;
    --text: #4a4a4a;
  }
  * { box-sizing: border-box; margin: 0; padding: 0; }
  html, body { width: 1200px; height: 1000px; overflow: hidden; }
  body {
    background: var(--bg);
    font-family: "Jost", sans-serif;
    position: relative;
  }
  .card {
    position: absolute;
    width: 540px;
    height: 310px;
    background: var(--card);
    box-shadow: 0 10px 30px rgba(0,0,0,0.25);
    overflow: hidden;
  }
  .card--back { left: 70px; top: 140px; }
  .card--front { left: 590px; top: 540px; }

  /* back side */
  .band { position: absolute; left: 0; right: 0; }
  .band--lime { top: 34px; height: 14px; background: var(--lime); }
  .band--charcoal { bottom: 40px; height: 9px; background: var(--charcoal); }

  .contact {
    position: absolute;
    top: 72px; left: 0; right: 0;
    text-align: center;
    color: var(--text);
    font-size: 13px;
    line-height: 21px;
    font-weight: 400;
  }
  .contact .label { font-style: italic; font-weight: 600; }

  .brand {
    position: absolute;
    left: 0; right: 0; top: 196px;
    display: flex; align-items: center; justify-content: center; gap: 10px;
  }
  .brand__mark { width: 22px; height: 22px; background: var(--lime); }
  .brand__name {
    font-size: 28px; font-weight: 700; letter-spacing: 1px;
    color: var(--charcoal);
  }

  /* front side */
  .front-brand {
    position: absolute; left: 44px; top: 92px;
    display: flex; align-items: center; gap: 14px;
  }
  .front-brand__mark { width: 46px; height: 46px; background: var(--lime); }
  .front-brand__name { font-size: 36px; font-weight: 700; color: var(--charcoal); letter-spacing: 1px; }

  .person {
    position: absolute; right: 30px; top: 138px;
    text-align: left;
  }
  .person__name { font-size: 36px; font-weight: 300; color: var(--text); line-height: 1; }
  .person__title { font-size: 17px; font-weight: 700; color: var(--charcoal); margin-top: 4px; }

  .rule { position: absolute; top: 214px; height: 3px; }
  .rule--lime-left { left: 0; width: 330px; background: var(--lime); }
  .rule--charcoal { left: 330px; width: 170px; background: var(--charcoal); }
  .rule--lime-right { left: 500px; right: 0; background: var(--lime); }
</style>
</head>
<body>
  <section class="card card--back" aria-label="Card back: contact details">
    <div class="band band--lime"></div>
    <div class="contact">
      <p><span class="label">MB:</span> +61 427 315 964</p>
      <p><span class="label">PH:</span> 1300 647 519</p>
      <p><span class="label">Email:</span> stuart.kovan@pellmora.com.au</p>
      <p><span class="label">Address:</span> 27D Halden Parade, Brookvale VIC 3174 Australia</p>
      <p><span class="label">Website:</span> www.pellmora.com.au</p>
    </div>
    <div class="brand">
      <span class="brand__mark"></span>
      <span class="brand__name">PELLMORA</span>
    </div>
    <div class="band band--charcoal"></div>
  </section>

  <section class="card card--front" aria-label="Card front: name and title">
    <div class="front-brand">
      <span class="front-brand__mark"></span>
      <span class="front-brand__name">PELLMORA</span>
    </div>
    <div class="person">
      <p class="person__name">Stuart Kovan</p>
      <p class="person__title">Director</p>
    </div>
    <div class="rule rule--lime-left"></div>
    <div class="rule rule--charcoal"></div>
    <div class="rule rule--lime-right"></div>
  </section>
</body>
</html>
```